Dental Medical History Form - Content provided

Design a medical history form for a dental practice. Content is provided so all that is needed is the formatting to make it look great and easy to read.

"Patient Information" to include all information contained in top portion of the "Patient Medical History Form" docx file.

"Medical History" should follow the formatting and content of the "Exact Medical History" file as this is what the entry fields look like in our practice software and so we would like it to match.

1st page - Patient info, allergies, medications, antibiotics, joint replacement, pregnancy.

2nd page - Do you have, or have you had, any of the following? . . . . . . .
Updates

Target Market(s)

All ages but must be clear enough for elderly to read. Use as much space as possible to keep font size bigger yet keep to two pages

Industry/Entity Type

Dental

Font styles to use
Sans Serif

Requirements
Must have
• All content provided
• Our logo at the top (file provided)
• Century Gothic Font
• Limit to two pages

```html
<!DOCTYPE html>
<html lang="en">
<head>
<meta charset="utf-8">
<title>Northbay Dental – Patient Medical History</title>
<link href="https://fonts.googleapis.com/css2?family=Mulish:wght@300;400;700&display=swap" rel="stylesheet">
<style>
  :root{
    --ink:#2f2f2f;
    --label:#3a3a3a;
    --soft:#6a6a6a;
    --rule:#4a4a4a;
    --box:#c4c4c4;
    --panel:#f2f2f2;
    --card-edge:#e2e2e2;
    --paper:#ffffff;
    --brand:#3b3b3b;
    --brand-mark:#9a8a78;
  }
  *{box-sizing:border-box;margin:0;padding:0}
  html,body{width:849px;height:1200px;overflow:hidden;background:var(--paper)}
  body{font-family:"Mulish",sans-serif;color:var(--ink);position:relative}
  .abs{position:absolute}

  /* header */
  .brand{left:50px;top:78px;display:flex;align-items:center;gap:14px}
  .brand-mark{width:26px;height:26px;background:var(--brand-mark);flex:none}
  .brand-name{font-size:40px;font-weight:300;color:var(--brand);line-height:1;white-space:nowrap}
  .practice-info{right:53px;top:61px;text-align:right;font-weight:700;font-size:14px;line-height:22px;color:var(--label);font-style:normal}

  /* patient panel */
  .panel{left:19px;top:160px;width:811px;height:406px;background:var(--panel)}
  .card{top:178px;height:370px;background:var(--paper);border:1px solid var(--card-edge)}
  .card-patient{left:38px;width:381px}
  .card-gp{left:432px;width:382px}

  .field{position:absolute;display:flex;align-items:baseline;font-size:12.5px}
  .field .lbl{font-weight:700;color:var(--label);white-space:nowrap}
  .field .colon{font-weight:700;margin:0 6px 0 0}
  .field .line{flex:1;border-bottom:1px solid var(--rule);height:1px;transform:translateY(3px)}
  .field .sub{color:var(--soft);font-size:13px;margin-right:8px;white-space:nowrap}
  .heading{position:absolute;font-weight:700;font-size:12.5px;color:var(--label)}
  .hint{position:absolute;font-size:11px;color:var(--soft)}

  .box{display:inline-block;width:22px;height:19px;border:1px solid var(--box);background:#fff;flex:none}
  .gp-choice{position:absolute;display:flex;align-items:center;font-size:12.5px;gap:6px}
  .gp-choice b{color:var(--label)}
  .gp-choice .or{color:var(--soft);margin:0 6px}

  /* history */
  .question{position:absolute;left:51px;font-weight:700;font-size:12.5px;color:var(--label);display:flex;align-items:center;gap:5px}
  .tick{width:18px;height:18px}
  .opt{position:absolute;display:flex;align-items:center;font-size:13px;color:var(--soft);gap:9px}
  .entry{position:absolute;left:119px;width:665px;height:25px;border:1px solid #d4d4d4;background:#fff}
  .yn-label{position:absolute;left:51px;font-weight:700;font-size:12.5px;color:var(--label)}
</style>
</head>
<body>

<header>
  <div class="abs brand"><span class="brand-mark"></span><span class="brand-name">Northbay Dental</span></div>
  <address class="abs practice-info">
    Northbay Dental<br>3.05/118 Seaview Parade<br>Avoca Bay NSW 2251<br>(02) 40 555 019
  </address>
</header>

<section class="abs panel"></section>
<section class="abs card card-patient"></section>
<section class="abs card card-gp"></section>

<!-- patient details -->
<div class="field" style="left:51px;top:200px;width:363px"><span class="lbl" style="width:105px">Name</span><span class="colon">:</span><span class="line"></span></div>
<span class="hint" style="left:164px;top:221px">Title</span>
<span class="hint" style="left:204px;top:221px">First</span>
<span class="hint" style="left:277px;top:221px">Middle</span>
<span class="hint" style="left:368px;top:221px">Last</span>
<div class="field" style="left:51px;top:250px;width:363px"><span class="lbl" style="width:105px">Address</span><span class="colon">:</span><span class="line"></span></div>
<div class="field" style="left:164px;top:274px;width:250px"><span class="line"></span></div>
<div class="field" style="left:51px;top:299px;width:363px"><span class="lbl" style="width:105px">DOB</span><span class="colon">:</span><span class="line"></span></div>
<div class="field" style="left:51px;top:324px;width:363px"><span class="lbl" style="width:105px">Email Address</span><span class="colon">:</span><span class="line"></span></div>
<div class="field" style="left:51px;top:349px;width:363px"><span class="lbl" style="width:105px">Phone Numbers</span><span class="colon">:</span><span class="sub" style="width:43px">Mobile</span><span class="line"></span></div>
<div class="field" style="left:166px;top:373px;width:248px"><span class="sub" style="width:41px">Work</span><span class="line"></span></div>
<div class="field" style="left:166px;top:398px;width:248px"><span class="sub" style="width:41px">Home</span><span class="line"></span></div>

<h2 class="heading" style="left:51px;top:447px">EMERGENCY CONTACT PERSON</h2>
<div class="field" style="left:51px;top:472px;width:363px"><span class="lbl" style="width:100px">Name</span><span class="colon">:</span><span class="line"></span></div>
<div class="field" style="left:51px;top:497px;width:363px"><span class="lbl" style="width:100px">Relationship</span><span class="colon">:</span><span class="line"></span></div>
<div class="field" style="left:51px;top:522px;width:363px"><span class="lbl" style="width:100px">Phone number</span><span class="colon">:</span><span class="line"></span></div>

<!-- general practitioner -->
<h2 class="heading" style="left:448px;top:198px">GENERAL PRACTITIONER</h2>
<div class="field" style="left:448px;top:231px;width:350px"><span class="lbl" style="width:101px">Name</span><span class="colon">:</span><span class="line"></span></div>
<div class="field" style="left:448px;top:264px;width:350px"><span class="lbl" style="width:101px">Practice Name</span><span class="colon">:</span><span class="line"></span></div>
<div class="field" style="left:448px;top:296px;width:350px"><span class="lbl" style="width:101px">Phone Number</span><span class="colon">:</span><span class="line"></span></div>
<h3 class="heading" style="left:448px;top:329px">Do you have a health fund with dental cover?</h3>
<div class="gp-choice" style="left:549px;top:361px"><span class="box"></span><b>Yes</b><span class="or">or</span><span class="box"></span><b>No</b></div>
<div class="field" style="left:448px;top:394px;width:350px"><span class="lbl" style="margin-right:6px">If so, what is the name of the fund ?</span><span class="line"></span></div>
<div class="field" style="left:448px;top:427px;width:350px"><span class="lbl" style="width:101px">Fund Number?</span><span class="colon">:</span><span class="line"></span></div>
<div class="gp-choice" style="left:448px;top:458px"><b>Priority Number on card &nbsp;: 0 &nbsp;1 &nbsp;2 &nbsp;3 &nbsp;4 &nbsp;5</b><span class="box" style="margin-left:14px"></span></div>
<div class="field" style="left:448px;top:492px;width:350px"><span class="lbl" style="width:101px">Occupation</span><span class="colon">:</span><span class="line"></span></div>
<div class="field" style="left:448px;top:525px;width:350px"><span class="lbl" style="width:101px">Referrred by</span><span class="colon">:</span><span class="line"></span></div>

<!-- allergies -->
<h2 class="question" style="top:588px">Please indicate if you are allergic to any of the following
  <svg class="tick" viewBox="0 0 18 18"><rect x="1" y="2" width="15" height="15" fill="none" stroke="#333" stroke-width="1.4"/><path d="M4 9l4 5 8-13" fill="none" stroke="#333" stroke-width="2"/></svg> ?</h2>
<div class="opt" style="left:119px;top:613px"><span class="box"></span>Aspirin</div>
<div class="opt" style="left:297px;top:613px"><span class="box"></span>Codeine</div>
<div class="opt" style="left:467px;top:613px"><span class="box"></span>Penicillin</div>
<div class="opt" style="left:649px;top:613px"><span class="box"></span>Sulfites</div>
<div class="opt" style="left:119px;top:639px"><span class="box"></span>Latex</div>
<div class="opt" style="left:297px;top:639px"><span class="box"></span>Local Anaesthetic</div>
<div class="opt" style="left:467px;top:639px"><span class="box"></span>Lactose</div>
<div class="opt" style="left:649px;top:639px"><span class="box"></span>Nickel</div>
<span class="yn-label" style="top:676px">Other</span>
<div class="entry" style="top:674px;height:26px"></div>

<!-- medications -->
<h2 class="question" style="top:717px">Are you currently taking, or have ever taken, any of the following medication
  <svg class="tick" viewBox="0 0 18 18"><rect x="1" y="2" width="15" height="15" fill="none" stroke="#333" stroke-width="1.4"/><path d="M4 9l4 5 8-13" fill="none" stroke="#333" stroke-width="2"/></svg> ?</h2>
<div class="opt" style="left:119px;top:748px"><span class="box"></span>Asthma inhaler</div>
<div class="opt" style="left:297px;top:748px"><span class="box"></span>Anti-epileptics</div>
<div class="opt" style="left:467px;top:748px"><span class="box"></span>Anti-depressants</div>
<div class="opt" style="left:649px;top:748px"><span class="box"></span>Blood Pressure</div>
<div class="opt" style="left:119px;top:777px"><span class="box"></span>Blood Thinners</div>
<div class="opt" style="left:297px;top:777px"><span class="box"></span>Bisphosphonates</div>
<div class="opt" style="left:467px;top:777px"><span class="box"></span>Chemotherapy</div>
<div class="opt" style="left:649px;top:777px"><span class="box"></span>Insulin</div>
<div class="opt" style="left:119px;top:807px"><span class="box"></span>Immunosuppressants</div>
<div class="opt" style="left:297px;top:807px"><span class="box"></span>Steroids</div>
<div class="opt" style="left:467px;top:807px"><span class="box"></span>Oral Contraceptive</div>
<div class="opt" style="left:649px;top:807px"><span class="box"></span>Other</div>

<h2 class="question" style="top:870px">Please specify medication name, dose, and frequency where possible:</h2>
<div class="entry" style="top:898px"></div>
<div class="entry" style="top:931px"></div>
<div class="entry" style="top:964px"></div>

<!-- yes / no -->
<span class="yn-label" style="top:1023px">Do you require antibiotic cover ?</span>
<div class="opt" style="left:297px;top:1021px"><span class="box"></span>Yes</div>
<div class="opt" style="left:370px;top:1021px"><span class="box"></span>No</div>
<span class="yn-label" style="top:1048px">Have you had a joint replacement?</span>
<div class="opt" style="left:297px;top:1046px"><span class="box"></span>Yes</div>
<div class="opt" style="left:370px;top:1046px"><span class="box"></span>No</div>
<span class="yn-label" style="top:1073px">WOMEN</span>
<span class="yn-label" style="top:1098px">Are you pregnant?</span>
<div class="opt" style="left:297px;top:1096px"><span class="box"></span>Yes</div>
<div class="opt" style="left:370px;top:1096px"><span class="box"></span>No</div>
<div class="opt" style="left:437px;top:1096px"><span class="box"></span>Possible</div>
<span class="yn-label" style="top:1122px">Breast Feeding?</span>
<div class="opt" style="left:297px;top:1120px"><span class="box"></span>Yes</div>
<div class="opt" style="left:370px;top:1120px"><span class="box"></span>No</div>

</body>
</html>
```